Site for entrepreneurs/small businesses needs Logo, Homepage

Looking for a logo, either an icon, or stylized text, or a combination of both, and a home page design which fits with it. The logo will be for use on the public website as well as for printed collateral (business cards, post cards, brochures and various other marketing materials).

The site is called Orbitwell (Orbitwell.example). This is to be a national, and eventually an international brand. The new service will provide an easy-to-use platform for entrepreneurs to build their business and web presence together in an integrated way which allows them to focus on their core competency.

The site/service will be dead-simple to use, A/B/C, 1/2/3. We will want some sort of "Get started for FREE" promotional space to collect the person's email address with multiple points of interest which guide the user back to this one call to action: sign up for free. We will feature editorial/blog stories, customer testimonials, and present several key features the the reader just can't live without if they are starting a new business.

Criteria:
* Refer to our comparable sites/logos in the design document attached
* Incorporate our color scheme (but complementary colors welcome)
* No Serif fonts!
* No photo-realistic elements for logo
* Logo must present well in gray scale and/or black/white (for printed materials)
* Strokes/borders that are wider to promote simplicity (vs. thin/precise lines which promote technical complexity)

Inspirations:
* Creative/Custom (but legible) fonts
* Excitement, energetic, jumping for joy
* Karate / Ninja / Power / Precision
* Dance Moves
* Regional influences: California, Silicon Valley, West Coast, Surf City, Beaches, Sunset
* Simple/easy, no-brainer solutions

Target Market(s)

Small Businesses / Entrepreneurs

Logo Text

Orbitwell or Orbitwell.example

Number of Pages Required

1 page

Font styles to use
Sans Serif
Decorative

Requirements
Must have
• See the attached style guide (PDF)

```html
<!DOCTYPE html>
<html lang="en">
<head>
<meta charset="utf-8">
<title>Orbitwell — Build your business and web presence</title>
<link href="https://fonts.googleapis.com/css2?family=Montserrat:wght@400;500;700&family=Open+Sans:wght@400;600;700&display=swap" rel="stylesheet">
<style>
:root{
  --navy:#14305e;
  --sky:#6fcdf2;
  --purple-a:#5b0f8e;
  --purple-b:#3a0868;
  --lavender:#e9cdf6;
  --magenta:#c22ad0;
  --orange-a:#f7a21b;
  --orange-b:#ee7a08;
  --orange-text:#e27d0b;
  --blue-a:#2d5fa9;
  --blue-b:#173e84;
  --text:#555;
  --dark:#333;
  --grey-bg:#efefef;
  --footer:#222;
}
*{box-sizing:border-box;margin:0;padding:0}
html,body{width:1200px;height:4054px;overflow:hidden;background:#fff}
body{position:relative;font-family:"Open Sans",Arial,sans-serif;color:var(--text)}
.abs{position:absolute}
.shape{position:absolute;left:0;top:0}
.brand{left:135px;top:20px;display:flex;align-items:center;gap:12px;font-family:"Montserrat",sans-serif;font-weight:500;font-size:34px;color:var(--navy)}
.brand-mark{width:32px;height:32px;background:var(--navy);border-radius:6px}
.nav{left:486px;top:14px;width:582px;height:54px;background:#fff;border:1px solid #e3e3e3;display:flex;align-items:center;justify-content:space-around;padding:0 10px;font-size:13px;color:#666;text-transform:uppercase}
.nav .current{color:var(--orange-b);font-weight:600}
.hero-kicker{left:135px;top:232px;font-family:"Montserrat",sans-serif;font-size:30px;color:var(--navy)}
.hero-title{left:135px;top:268px;font-family:"Montserrat",sans-serif;font-weight:700;font-size:38px;color:var(--navy)}
.hero-copy{left:135px;top:320px;width:460px;font-size:13.5px;line-height:19px;color:#444}
.btn-start{left:135px;top:400px;width:200px;height:36px;border-radius:18px;background:var(--navy);color:#fff;font-size:13px;font-weight:600;display:flex;align-items:center;justify-content:center;text-transform:uppercase}
.pager{top:462px;width:26px;height:30px;display:flex;align-items:center;justify-content:center}
.pager.prev{left:135px;background:#ccc}
.pager.next{left:163px;background:#333}
.illus{border-radius:8px}
.section-title{font-family:"Montserrat",sans-serif;font-weight:700;font-size:37px;text-transform:uppercase}
.signup-title{left:135px;top:822px;color:#fff}
.field{left:135px;width:325px;background:var(--lavender);color:var(--purple-a);font-size:14px;padding:10px 16px}
.btn-signup{left:135px;top:1170px;width:97px;height:38px;border-radius:19px;background:linear-gradient(#d63be0,#a31cb5);color:#fff;font-size:13px;font-weight:600;display:flex;align-items:center;justify-content:center;text-transform:uppercase}
.signup-copy{left:654px;top:1068px;width:414px;font-size:15px;line-height:27.5px;color:#555}
.features-title{right:132px;top:1730px;color:var(--navy)}
.features-copy{right:132px;top:1786px;width:370px;text-align:right;font-size:15px;line-height:27.5px;color:var(--navy)}
.feature{left:135px;width:460px;display:flex;gap:32px}
.feature svg{flex:none;width:62px;height:62px}
.feature h3{font-family:"Montserrat",sans-serif;font-weight:400;font-size:29px;color:var(--orange-text);line-height:34px}
.feature p{font-size:13.5px;line-height:19px;color:#555}
.testi-title{left:135px;top:2563px;color:#fff}
.quote-marks{left:130px;top:2600px;font-family:"Montserrat",sans-serif;font-weight:700;font-size:200px;line-height:200px;color:#fff;letter-spacing:40px}
.quote{left:654px;width:414px;font-size:20px;line-height:33px;color:#444}
.quote cite{display:block;margin-top:10px;font-style:normal;color:var(--blue-a)}
.rule{left:527px;width:541px;height:2px;background:#ddd}
.blog-band{left:0;top:3319px;width:1200px;height:636px;background:var(--grey-bg)}
.blog-title{left:0;top:3404px;width:1200px;text-align:center;color:var(--navy)}
.card{top:3473px;width:298px}
.card .thumb{display:block;width:298px;height:217px}
.card h4{margin-top:12px;font-size:14px;line-height:19px;color:#222;font-weight:600}
.card p{margin-top:8px;font-size:10.5px;line-height:14px;color:#555}
.btn-more{display:inline-flex;margin-top:12px;width:86px;height:36px;border-radius:18px;background:#ccc;color:#333;font-size:11px;font-weight:600;align-items:center;justify-content:center;text-transform:uppercase}
.slide-arrow{top:3560px}
.footer{left:0;top:3955px;width:1200px;height:99px;background:var(--footer)}
.footer-links{left:135px;top:3980px;font-size:11.5px;color:#999}
.footer-links span{margin:0 8px;color:#666}
.copyright{left:135px;top:4008px;font-size:11.5px;color:#888}
.social{top:3990px;width:26px;height:26px;border-radius:50%}
</style>
</head>
<body>

<!-- Hero background -->
<svg class="shape" width="1200" height="640" aria-hidden="true">
  <path d="M351 0 H1200 V420 L1035 590 Q1005 622 975 592 Z" fill="var(--sky)"/>
</svg>
<div class="abs illus" role="img" aria-label="Illustration of a thoughtful businessman surrounded by idea icons" style="left:760px;top:150px;width:360px;height:430px;background:radial-gradient(circle at 50% 45%,#ffffff55,#6fcdf200 70%)"></div>

<header>
  <div class="abs brand"><span class="brand-mark"></span>Orbitwell</div>
  <nav class="abs nav">
    <span class="current">Home</span><span>About us</span><span>Services</span><span>Solutions</span><span>Portfolio</span><span>Contact us</span>
  </nav>
</header>

<section class="hero">
  <div class="abs hero-kicker">Vestibulum condimentum</div>
  <h1 class="abs hero-title">RISUS POSUERE CURSUS</h1>
  <p class="abs hero-copy">Nullam lorem urna, tempus eget mollis et, dapibus ac sem. Suspendisse gravida ornare erat sed pulvinar. Vestibulum luctus ex in egestas fringilla. Fusce nec leo ac urna pulvinar auctor.</p>
  <div class="abs btn-start">Get started for free</div>
  <div class="abs pager prev"><svg width="10" height="14"><path d="M8 1 L2 7 L8 13" stroke="#fff" stroke-width="2" fill="none"/></svg></div>
  <div class="abs pager next"><svg width="10" height="14"><path d="M2 1 L8 7 L2 13" stroke="#fff" stroke-width="2" fill="none"/></svg></div>
</section>

<!-- Signup -->
<svg class="shape" width="1200" height="1500" aria-hidden="true">
  <defs><linearGradient id="gPurple" x1="0" y1="0" x2="1" y2="1"><stop offset="0" stop-color="var(--purple-a)"/><stop offset="1" stop-color="var(--purple-b)"/></linearGradient></defs>
  <path d="M0 620 L555 828 Q600 846 580 890 L300 1445 Q285 1480 250 1470 L0 1355 Z" fill="url(#gPurple)"/>
</svg>
<section class="signup">
  <h2 class="abs section-title signup-title">Signup for free</h2>
  <div class="abs field" style="top:887px;height:48px">Full Name</div>
  <div class="abs field" style="top:949px;height:48px">Email Address</div>
  <div class="abs field" style="top:1014px;height:135px">Message</div>
  <div class="abs btn-signup">Sign up</div>
  <div class="abs illus" role="img" aria-label="Illustration of a document with a pencil" style="left:654px;top:833px;width:190px;height:202px;background:linear-gradient(135deg,#eee8da,#d8cfbd)"></div>
  <p class="abs signup-copy">Vestibulum condimentum, risus ut posuere cursus, velit justo accumsan sem, lobortis aliquet metus dui eu libero. Pellentesque a imperdiet dolor, et auctor est. Fusce sollicitudin lorem et luctus volutpat. Proin placerat dapibus gravida. In tristique tristique nulla eget hendrerit. Maecenas vel tortor accumsan quam varius imperdiet vel eget elit. Aenean facilisis tincidunt lectus, id dictum nisi luctus eget. Vivamus efficitur ex condimentum, malesuada eros eget, feugiat nibh.</p>
</section>

<!-- Key features -->
<svg class="shape" width="1200" height="2400" aria-hidden="true">
  <defs><linearGradient id="gOrange" x1="0" y1="0" x2="1" y2="1"><stop offset="0" stop-color="var(--orange-a)"/><stop offset="1" stop-color="var(--orange-b)"/></linearGradient></defs>
  <path d="M805 1495 Q825 1460 865 1478 L1200 1622 V2325 L635 2090 Q598 2075 612 2040 Z" fill="url(#gOrange)"/>
</svg>
<section class="features">
  <h2 class="abs section-title features-title">Key features</h2>
  <p class="abs features-copy">Sed tellus ex, imperdiet eget gravida sit amet, volutpat eget turpis. In nec ultricies est. Etiam mattis augue vehicula odio posuere, sit amet tempus lectus luctus. Nulla facilisi. Etiam vel massa elementum, bibendum tellus venenatis, feugiat massa. Curabitur venenatis lacinia ornare. Cras sollicitudin cursus dui eu placerat.</p>

  <div class="abs feature" style="top:1610px">
    <svg viewBox="0 0 62 62"><circle cx="31" cy="25" r="15" fill="#f6c12b"/><rect x="24" y="40" width="14" height="10" rx="2" fill="#888"/></svg>
    <div><h3>Aliquam erat</h3><p>Quisque aliquet ex nec est vestibulum pulvinar.<br>Pellentesque convallis molestie enim sit amet efficitur</p></div>
  </div>
  <div class="abs feature" style="top:1732px">
    <svg viewBox="0 0 62 62"><circle cx="26" cy="26" r="16" fill="none" stroke="#3aa5dd" stroke-width="8" stroke-dasharray="6 4"/><circle cx="44" cy="44" r="9" fill="none" stroke="#e8543a" stroke-width="5"/></svg>
    <div><h3>Vivamus lacus</h3><p>Quisque aliquet ex nec est vestibulum pulvinar.<br>Pellentesque convallis molestie enim sit amet efficitur</p></div>
  </div>
  <div class="abs feature" style="top:1867px">
    <svg viewBox="0 0 62 62"><circle cx="31" cy="31" r="22" fill="none" stroke="#f39c12" stroke-width="10" stroke-dasharray="46 100"/><circle cx="31" cy="31" r="22" fill="none" stroke="#8cc63f" stroke-width="10" stroke-dasharray="0 46 46 100"/><circle cx="31" cy="31" r="22" fill="none" stroke="#3aa5dd" stroke-width="10" stroke-dasharray="0 92 46 100"/></svg>
    <div><h3>Fusce vitae</h3><p>Quisque aliquet ex nec est vestibulum pulvinar.<br>Pellentesque convallis molestie enim sit amet efficitur</p></div>
  </div>
  <div class="abs feature" style="top:2002px">
    <svg viewBox="0 0 62 62"><circle cx="31" cy="31" r="24" fill="#3a8fd8"/><path d="M18 22 Q26 16 32 24 Q28 34 20 32 Z M36 36 Q46 34 46 44 Q38 48 36 36 Z" fill="#9ed0f5"/></svg>
    <div><h3>Aenean</h3><p>Quisque aliquet ex nec est vestibulum pulvinar.<br>Pellentesque convallis molestie enim sit amet efficitur</p></div>
  </div>
  <div class="abs feature" style="top:2145px">
    <svg viewBox="0 0 62 62"><g stroke="#555" stroke-width="2"><line x1="31" y1="31" x2="14" y2="14"/><line x1="31" y1="31" x2="50" y2="12"/><line x1="31" y1="31" x2="12" y2="50"/><line x1="31" y1="31" x2="50" y2="48"/></g><circle cx="31" cy="31" r="6" fill="#7b3fa0"/><circle cx="14" cy="14" r="5" fill="#e74c3c"/><circle cx="50" cy="12" r="5" fill="#3aa5dd"/><circle cx="12" cy="50" r="5" fill="#8cc63f"/><circle cx="50" cy="48" r="5" fill="#f39c12"/></svg>
    <div><h3>Phasellus nisl</h3><p>Quisque aliquet ex nec est vestibulum pulvinar.<br>Pellentesque convallis molestie enim sit amet efficitur</p></div>
  </div>
</section>

<!-- Testimonials -->
<svg class="shape" width="1200" height="3300" aria-hidden="true">
  <defs><linearGradient id="gBlue" x1="0" y1="0" x2="1" y2="1"><stop offset="0" stop-color="var(--blue-a)"/><stop offset="1" stop-color="var(--blue-b)"/></linearGradient></defs>
  <path d="M0 2360 L560 2545 Q598 2560 585 2598 L380 3190 Q365 3225 330 3212 L0 3095 Z" fill="url(#gBlue)"/>
</svg>
<section class="testimonials">
  <h2 class="abs section-title testi-title">Testimonials</h2>
  <div class="abs quote-marks" aria-hidden="true">“ ”</div>
  <blockquote class="abs quote" style="top:2560px">“ Nunc sit amet consequat risus. Curabitur ac elit leo. In eleifend dui tellus, in scelerisque elit porttitor et. Integer eu massa lacinia, lacinia nulla non, volutpat purus. ”<cite>- Marcus Hale, Company name</cite></blockquote>
  <div class="abs rule" style="top:2784px"></div>
  <blockquote class="abs quote" style="top:2815px">“ Aenean sed quam non sapien faucibus consequat vitae sit amet orci. Praesent quis risus mi. In mollis nulla in pulvinar dictum. Vivamus interdum sagittis felis, ut dapibus ligula feugiat ac. In dictum sapien eu tellus finibus fermentum ”<cite>- Renata Voss, Company name</cite></blockquote>
  <div class="abs rule" style="top:3090px"></div>
  <svg class="abs" style="left:652px;top:3132px" width="36" height="22" aria-hidden="true"><path d="M3 3 L18 18 L33 3" stroke="#999" stroke-width="4" fill="none"/></svg>
</section>

<!-- Blog -->
<section>
  <div class="abs blog-band"></div>
  <h2 class="abs section-title blog-title">Blog</h2>
  <svg class="abs slide-arrow" style="left:48px" width="22" height="40" aria-hidden="true"><path d="M18 3 L4 20 L18 37" stroke="#999" stroke-width="4" fill="none"/></svg>
  <svg class="abs slide-arrow" style="left:1130px" width="22" height="40" aria-hidden="true"><path d="M4 3 L18 20 L4 37" stroke="#999" stroke-width="4" fill="none"/></svg>

  <article class="abs card" style="left:135px">
    <span class="thumb" role="img" aria-label="Illustration of business people climbing toward a goal" style="background:linear-gradient(160deg,#4cb3dc,#2a8fbf)"></span>
    <h4>Quisque aliquet ex nec est vestibulum pulvinar.</h4>
    <p>Vestibulum condimentum, risus posuere cursus, Pellentesque a imperdiet dolor, et auctor. Fusce sollicitudin lorem et luctus volutpat. Proin placerat dapibus gravida.</p>
    <span class="btn-more">Read more</span>
  </article>
  <article class="abs card" style="left:451px">
    <span class="thumb" role="img" aria-label="Illustration of a team meeting beside a presentation board" style="background:linear-gradient(160deg,#ffffff,#e4eef4)"></span>
    <h4>Aliquam dignissim elit nec mauris porta, vitae pretium risus placerat</h4>
    <p>Vestibulum condimentum, risus posuere cursus, Pellentesque a imperdiet dolor, et auctor. Fusce sollicitudin lorem et luctus volutpat. Proin placerat dapibus gravida.</p>
    <span class="btn-more">Read more</span>
  </article>
  <article class="abs card" style="left:770px">
    <span class="thumb" role="img" aria-label="Illustration of colleagues working together in a city" style="background:linear-gradient(160deg,#3fa9d6,#1f7fb0)"></span>
    <h4>Nulla porttitor nibh ut mi feugiat rhoncus quis in ante</h4>
    <p>Vestibulum condimentum, risus posuere cursus, Pellentesque a imperdiet dolor, et auctor. Fusce sollicitudin lorem et luctus volutpat. Proin placerat dapibus gravida.</p>
    <span class="btn-more">Read more</span>
  </article>
</section>

<footer>
  <div class="abs footer"></div>
  <div class="abs footer-links">Home<span>|</span>About Us<span>|</span>Services<span>|</span>Solutions<span>|</span>Portfolio<span>|</span>Contact Us</div>
  <div class="abs copyright">Copyright © 2016 Orbitwell. &nbsp; All rights reserved.</div>
  <span class="abs social" style="left:1008px;background:#3b5998"></span>
  <span class="abs social" style="left:1040px;background:#2aa3ef"></span>
</footer>

</body>
</html>
```